ecommerce news podcast artwork

Podcast cover art for a podcast featuring daily news and events around ecommerce product businesses.

text to be: BRISK LOOP
optional third line of text with smaller font: Podcast

looking for something that pops with a medium to light blue background. text can be in white/red/orange colors. prefer solid colors for text, but background can vary.
I'm really open to other ideas too, sometimes you don't know what you want until you see it.

Target Market(s)

ecommerce business owners, managers

Industry/Entity Type

news, business, ecommerce

Font styles to use
Sans Serif

Colors
0054AA
0677BA
7BADD7
CADEEF
E8F1F8
0094D4
00A9DD
6FCCEA
C7EBF8
E9F6FB
F0912C
F2A743
F7CA91
FBE8D2
FDF5EE
EB3D1F
EC4F4E
F09395
F8D3D4
FCEDEE

Requirements
Must have
• text: BRISK LOOP
Should not have
• no microphones, headsets/headphones, speakers, or other props like that.

```html
<!DOCTYPE html>
<html lang="en">
<head>
<meta charset="utf-8">
<title>Brisk Loop Podcast – Cover Art</title>
<link href="https://fonts.googleapis.com/css2?family=Archivo+Black&family=Archivo:wght@800;900&display=swap" rel="stylesheet">
<style>
  :root {
    --page: #ffffff;
    --sky-center: #f3fbfe;
    --sky-mid: #c7ebf8;
    --sky-edge: #86c9e8;
    --title-red: #dc0000;
    --title-red-shadow: #7a0b0b;
    --title-white: #ffffff;
    --ink: #111111;
    --art-warm: #f0912c;
    --art-red: #ec4f4e;
    --art-blue: #0094d4;
  }
  * { margin: 0; padding: 0; box-sizing: border-box; }
  html, body {
    width: 1032px;
    height: 1200px;
    overflow: hidden;
    background: var(--page);
  }
  .cover {
    position: absolute;
    left: 93px;
    top: 177px;
    width: 846px;
    height: 846px;
    overflow: hidden;
    background: radial-gradient(circle at 50% 52%, var(--sky-center) 0%, var(--sky-mid) 50%, var(--sky-edge) 100%);
  }
  .cart-artwork {
    position: absolute;
    left: 58px;
    top: 112px;
    width: 248px;
    height: 318px;
    border-radius: 40px;
    background: radial-gradient(circle at 50% 40%, var(--art-warm) 0%, var(--art-red) 40%, var(--art-blue) 100%);
    opacity: 0.55;
  }
  .title-badge {
    position: absolute;
    left: 318px;
    top: 265px;
    width: 481px;
    height: 179px;
    border-radius: 12px;
    background: var(--title-red);
  }
  .title-svg {
    position: absolute;
    left: 0;
    top: 0;
    width: 846px;
    height: 846px;
  }
  .title-top, .title-top-shadow {
    font-family: "Archivo Black", "Archivo", sans-serif;
    font-size: 142px;
  }
  .title-top { fill: var(--title-white); }
  .title-top-shadow { fill: var(--title-red-shadow); }
  .title-main {
    font-family: "Archivo Black", "Archivo", sans-serif;
    font-size: 275px;
    fill: var(--ink);
  }
  .subtitle {
    position: absolute;
    left: 0;
    width: 846px;
    top: 706px;
    text-align: center;
    font-family: "Archivo", sans-serif;
    font-weight: 900;
    font-size: 30px;
    letter-spacing: 0.62em;
    padding-left: 0.62em;
    color: var(--ink);
    text-transform: uppercase;
  }
</style>
</head>
<body>
  <div class="cover">
    <div class="cart-artwork" role="img" aria-label="Illustration of a shopping cart filled with colourful ecommerce icon bubbles"></div>

    <div class="title-badge"></div>

    <svg class="title-svg" viewBox="0 0 846 846" aria-label="Brisk Loop">
      <text class="title-top-shadow" x="385" y="418" textLength="354" lengthAdjust="spacingAndGlyphs">BRISK</text>
      <text class="title-top" x="378" y="411" textLength="354" lengthAdjust="spacingAndGlyphs">BRISK</text>
      <text class="title-main" x="76" y="657" textLength="722" lengthAdjust="spacingAndGlyphs">LOOP</text>
    </svg>

    <div class="subtitle">Podcast</div>
  </div>
</body>
</html>
```